Business Card Design Project

Business Card
We are rebranding with a new logo
Industry/Entity Type
Business
Contact Information for Business Card
Dennis Morvale +61 487215963 dennis@quorv.com.au P.O. Box 872 Fernlow QLD 4309
Requirements
Must have
- Logo

```html
<!DOCTYPE html>
<html lang="en">
<head>
<meta charset="utf-8">
<title>Quorv International – Business Card</title>
<link href="https://fonts.googleapis.com/css2?family=Questrial&display=swap" rel="stylesheet">
<style>
  :root {
    --stage: #3b3b3b;
    --navy: #0b4a6b;
    --navy-deep: #093f5c;
    --sky: #1282b0;
    --orange-deep: #de5f27;
    --orange: #f08a22;
    --paper: #fafafa;
    --paper-shade: #d9d9d9;
    --ink: #1f1f1f;
    --light: #ffffff;
  }
  * { margin: 0; padding: 0; box-sizing: border-box; }
  html, body {
    width: 1200px; height: 965px; overflow: hidden;
    background: var(--stage);
    font-family: "Questrial", "Century Gothic", sans-serif;
  }
  .card {
    position: absolute; left: 110px; top: 202px;
    width: 980px; height: 560px;
    border-radius: 46px; overflow: hidden;
    box-shadow: 0 6px 24px rgba(0,0,0,.45);
  }
  .card__art { position: absolute; inset: 0; }
  .brand {
    position: absolute; left: 60px; top: 200px; width: 400px;
    text-align: center; color: var(--ink);
    font-weight: 400; letter-spacing: 4px;
  }
  .brand__name { font-size: 78px; line-height: 1; letter-spacing: 6px; }
  .brand__sub { font-size: 28px; margin-top: 18px; }
  .details {
    position: absolute; right: 63px; top: 142px;
    color: var(--light); text-align: right;
  }
  .details__name { font-size: 29px; letter-spacing: .5px; margin-bottom: 52px; }
  .contact { list-style: none; font-size: 21px; line-height: 28px; }
  .contact li { display: flex; justify-content: flex-end; align-items: center; gap: 12px; }
  .contact svg { width: 22px; height: 20px; }
  .address { font-size: 21px; line-height: 28px; margin-top: 45px; }
</style>
</head>
<body>
  <div class="card">
    <svg class="card__art" viewBox="0 0 980 560" preserveAspectRatio="none">
      <defs>
        <linearGradient id="paperFade" x1="0" y1="0" x2="0" y2="1">
          <stop offset="0" stop-color="var(--paper)"/>
          <stop offset="1" stop-color="var(--paper-shade)"/>
        </linearGradient>
        <linearGradient id="navyFade" x1="0" y1="0" x2="0" y2="1">
          <stop offset="0" stop-color="var(--navy)"/>
          <stop offset="1" stop-color="var(--navy-deep)"/>
        </linearGradient>
      </defs>
      <rect width="980" height="560" fill="url(#navyFade)"/>
      <path d="M0,0 L545,0 C600,130 600,330 452,560 L0,560 Z" fill="var(--sky)"/>
      <path d="M0,0 L540,0 C585,140 575,330 390,560 L0,560 Z" fill="var(--orange-deep)"/>
      <path d="M0,0 L505,0 C555,150 545,340 375,560 L0,560 Z" fill="var(--orange)"/>
      <path d="M0,0 L460,0 C540,150 532,360 368,560 L0,560 Z" fill="url(#paperFade)"/>
    </svg>

    <div class="brand">
      <div class="brand__name">QUORV</div>
      <div class="brand__sub">INTERNATIONAL</div>
    </div>

    <div class="details">
      <p class="details__name">DENNIS MORVALE</p>
      <ul class="contact">
        <li>+61 487215963
          <svg viewBox="0 0 24 24" aria-hidden="true"><path fill="#fff" d="M6.6 10.8a15 15 0 0 0 6.6 6.6l2.2-2.2a1 1 0 0 1 1-.25 11.4 11.4 0 0 0 3.6.57 1 1 0 0 1 1 1V20a1 1 0 0 1-1 1A17 17 0 0 1 3 4a1 1 0 0 1 1-1h3.5a1 1 0 0 1 1 1c0 1.25.2 2.45.57 3.57a1 1 0 0 1-.25 1z"/></svg>
        </li>
        <li>dennis@quorv.com.au
          <svg viewBox="0 0 24 20" aria-hidden="true"><rect x="1" y="2" width="22" height="16" fill="#fff"/><path d="M1 2 L12 11 L23 2 M1 18 L9 9 M23 18 L15 9" stroke="var(--navy)" stroke-width="1.6" fill="none"/></svg>
        </li>
        <li>www.quorv.com.au
          <svg viewBox="0 0 24 24" aria-hidden="true"><g fill="none" stroke="#fff" stroke-width="1.8"><circle cx="12" cy="12" r="10"/><ellipse cx="12" cy="12" rx="4.5" ry="10"/><path d="M2 12h20M4 6.5h16M4 17.5h16"/></g></svg>
        </li>
      </ul>
      <p class="address">P.O. Box 872 Fernlow<br>QLD 4309</p>
    </div>
  </div>
</body>
</html>
```